BOLD & MINIMALIST DESIGN NEEDED

We want a very bold but minimalistic business card design that is impactful and utilizes both sides of the business card. Our current logo is included for your use.

We want bold fonts and good use of negative space. We don't want the logo to overpower the design.

Target Market(s)

Professionals who are building new commercial buildings.

Industry/Entity Type

Construction

Contact Information for Business Card

Name, Title, email, office phone, cell phone, website

Font styles to use
Serif
Sans Serif

Requirements
Must have
• Bold design!

```html
<!DOCTYPE html>
<html lang="en">
<head>
<meta charset="utf-8">
<title>Summitcrest Design + Build — Business Card</title>
<link href="https://fonts.googleapis.com/css2?family=Montserrat:wght@400;500;700;800&display=swap" rel="stylesheet">
<style>
  :root {
    --page-bg: #1f1f1f;
    --card-white: #ffffff;
    --brand-green: #84c341;
    --brand-green-light: #93cc55;
    --brand-green-deep: #4a7d3a;
    --ink: #1a1a1a;
    --ink-soft: #333333;
  }
  * { box-sizing: border-box; margin: 0; padding: 0; }
  html, body {
    width: 1200px;
    height: 1059px;
    overflow: hidden;
    background: var(--page-bg);
    font-family: "Montserrat", sans-serif;
  }
  .sheet { position: relative; width: 1200px; height: 1059px; }

  .card {
    position: absolute;
    width: 692px;
    height: 395px;
    border-radius: 26px;
    overflow: hidden;
  }
  .card--front { left: 255px; top: 89px; background: var(--card-white); }
  .card--back {
    left: 253px; top: 545px;
    background: linear-gradient(120deg, var(--brand-green) 0%, var(--brand-green-light) 45%, var(--brand-green) 100%);
  }

  /* Front: brand block */
  .brand {
    position: absolute;
    left: 60px; top: 150px;
    width: 300px;
    text-align: center;
  }
  .brand__mark {
    display: block;
    width: 22px; height: 22px;
    margin: 0 auto 14px;
    background: var(--brand-green);
  }
  .brand__name {
    font-weight: 800;
    font-size: 33px;
    letter-spacing: 0.5px;
    color: var(--ink);
    line-height: 1;
  }
  .brand__tagline {
    margin-top: 8px;
    font-weight: 800;
    font-size: 14px;
    letter-spacing: 6px;
    color: var(--ink);
  }

  .divider {
    position: absolute;
    left: 368px; top: 77px;
    width: 2px; height: 240px;
    background: var(--brand-green);
  }

  /* Front: contact block */
  .contact { position: absolute; left: 397px; top: 72px; color: var(--ink-soft); }
  .contact__name {
    font-weight: 700;
    font-size: 31px;
    color: var(--brand-green);
    letter-spacing: 0.5px;
    line-height: 1.05;
  }
  .contact__title { font-weight: 500; font-size: 17px; margin-top: 6px; letter-spacing: 0.5px; }
  .contact__address { font-size: 17.5px; line-height: 28px; margin-top: 14px; }
  .contact__list { list-style: none; margin-top: 14px; }
  .contact__item {
    display: flex; align-items: center;
    font-size: 18px; height: 27.5px;
  }
  .contact__icon { width: 15px; height: 15px; margin-right: 8px; flex: none; fill: var(--brand-green); }

  /* Back */
  .back-brand {
    position: absolute;
    left: 0; right: 0; top: 150px;
    text-align: center;
    color: var(--brand-green-deep);
  }
  .back-brand__name { font-weight: 800; font-size: 62px; line-height: 1; letter-spacing: 1px; }
  .back-brand__tagline { margin-top: 16px; font-weight: 800; font-size: 26px; letter-spacing: 12px; }
</style>
</head>
<body>
<main class="sheet">
  <section class="card card--front" aria-label="Card front">
    <div class="brand">
      <span class="brand__mark"></span>
      <div class="brand__name">SUMMITCREST</div>
      <div class="brand__tagline">DESIGN + BUILD</div>
    </div>

    <div class="divider"></div>

    <div class="contact">
      <h1 class="contact__name">MARCUS VELL</h1>
      <p class="contact__title">OWNER-CEO</p>
      <p class="contact__address">Your address, City<br>State, Zip 1234</p>
      <ul class="contact__list">
        <li class="contact__item">
          <svg class="contact__icon" viewBox="0 0 16 16"><path d="M1 6c0-2 3-3 7-3s7 1 7 3v1h-4V5.5H5V7H1zM4 8h8l2 5H2z"/></svg>
          123 456 789
        </li>
        <li class="contact__item">
          <svg class="contact__icon" viewBox="0 0 16 16"><path d="M4 0h8a1 1 0 0 1 1 1v14a1 1 0 0 1-1 1H4a1 1 0 0 1-1-1V1a1 1 0 0 1 1-1zm1 2v10h6V2zm3 11a1 1 0 1 0 0 2 1 1 0 0 0 0-2z"/></svg>
          123 456 789
        </li>
        <li class="contact__item">
          <svg class="contact__icon" viewBox="0 0 16 16"><path d="M0 3h16v10H0zm1.5 1.2L8 9l6.5-4.8V4h-13z"/></svg>
          info@yourgmail.com
        </li>
        <li class="contact__item">
          <svg class="contact__icon" viewBox="0 0 16 16"><circle cx="8" cy="8" r="7.5"/><path d="M4 5l3 1-1 3 2 2-1 3M10 2l1 3 3 1" stroke="#fff" stroke-width="1.2" fill="none"/></svg>
          www.yourwebsite.com
        </li>
      </ul>
    </div>
  </section>

  <section class="card card--back" aria-label="Card back">
    <div class="back-brand">
      <div class="back-brand__name">SUMMITCREST</div>
      <div class="back-brand__tagline">DESIGN + BUILD</div>
    </div>
  </section>
</main>
</body>
</html>
```